Retail Jewelry Business Card Design Project

We are in need of a new business card design for a retail jewelry store. This store is in the business of fine jewelry including but not specific to bridal jewelry, diamonds, designer jewelry and watches.

This store has been in business for 20 years but continues to strive for a modern professional appeal. The main colors use for this business are a royal blue, white and silver.

Target Market(s)

Target market is ages 18-50

Industry/Entity Type

Jewelry

Requirements
Must have
• Sales Person Name
Sales Person Email Address

Store Address
Store Phone
Website

Standard business card size. No odd shapes or sizes.
Nice to have
• Overall modern feel for card.

We have thought that a design with a nice feature of the logo on the back of the card would be nice but open to ideas.
Should not have
• No specific images of jewelry should be used.

```html
<!DOCTYPE html>
<html lang="en">
<head>
<meta charset="utf-8">
<title>Aldren Hale Fine Jewelry – Business Card</title>
<link rel="stylesheet" href="https://fonts.googleapis.com/css2?family=Tinos:ital,wght@0,400;0,700;1,700&display=swap">
<style>
  :root {
    --royal: #2e3192;
    --lavender: #7b7fc4;
    --white: #ffffff;
    --silver: #d4d6e2;
    --backdrop: #ecebe8;
    --ink: #2b2b3a;
  }
  * { margin: 0; padding: 0; box-sizing: border-box; }
  html, body { width: 1200px; height: 804px; overflow: hidden; }
  body {
    background: var(--backdrop);
    font-family: "Tinos", "Times New Roman", serif;
    position: relative;
  }
  .card {
    position: absolute;
    width: 540px;
    height: 309px;
    overflow: hidden;
    box-shadow: 0 6px 18px rgba(0,0,0,0.18);
  }
  /* Front of card */
  .card-front { left: 40px; top: 110px; background: var(--white); }
  .card-front .swoosh { position: absolute; inset: 0; width: 540px; height: 309px; }
  .wordmark { color: var(--royal); font-weight: 400; line-height: 1; }
  .card-front .wordmark { position: absolute; left: 40px; top: 30px; }
  .wordmark-name { display: block; font-size: 46px; }
  .wordmark-tag {
    display: block; font-size: 20px; letter-spacing: 3px;
    margin-top: 6px; padding-top: 5px; padding-left: 30px;
    border-top: 2px solid var(--lavender);
  }
  .person-name {
    position: absolute; left: 44px; top: 142px;
    color: var(--royal); font-size: 16px; font-weight: 700; font-style: italic;
  }
  .contact-list { position: absolute; left: 44px; top: 172px; list-style: none; }
  .contact-list li {
    display: flex; align-items: center; gap: 8px;
    font-size: 14px; color: var(--ink); height: 20px;
  }
  .contact-list svg { width: 11px; height: 11px; flex: none; }
  .store-address {
    position: absolute; left: 398px; top: 150px;
    color: var(--white); font-size: 13px; line-height: 1.35;
  }
  /* Back of card */
  .card-back { left: 620px; top: 380px; background: var(--royal); text-align: center; }
  .card-back .wordmark { color: var(--white); position: absolute; left: 90px; right: 90px; top: 70px; }
  .card-back .wordmark-name { font-size: 62px; }
  .card-back .wordmark-tag {
    font-size: 24px; letter-spacing: 5px; margin-top: 8px; padding-top: 8px; padding-left: 0;
    border-top: 2px solid var(--white);
  }
  .back-domain {
    position: absolute; right: 60px; top: 200px;
    color: var(--silver); font-size: 13px; letter-spacing: 1px;
  }
  .back-website {
    position: absolute; left: 0; right: 0; bottom: 40px;
    color: var(--silver); font-size: 16px; letter-spacing: 3px;
  }
</style>
</head>
<body>

<section class="card card-front" aria-label="Business card front">
  <svg class="swoosh" viewBox="0 0 540 309" aria-hidden="true">
    <path d="M540 30 C 430 50, 400 120, 350 190 C 300 260, 200 290, 0 292 L0 309 L540 309 Z" fill="var(--royal)"/>
    <path d="M540 16 C 428 36, 392 108, 340 178 C 290 246, 190 276, 0 280" fill="none" stroke="var(--lavender)" stroke-width="5"/>
    <path d="M0 302 C 120 300, 220 288, 300 262" fill="none" stroke="var(--lavender)" stroke-width="4"/>
  </svg>

  <div class="wordmark">
    <span class="wordmark-name">Aldren Hale</span>
    <span class="wordmark-tag">FINE JEWELRY</span>
  </div>

  <p class="person-name">Aldren Hale Morrow</p>

  <ul class="contact-list">
    <li>
      <svg viewBox="0 0 12 12" aria-hidden="true"><circle cx="6" cy="6" r="6" fill="var(--royal)"/><path d="M4 3.2 L5 3 L5.6 4.6 L5 5.2 Q5.6 6.6 6.8 7 L7.4 6.4 L9 7 L8.8 8 Q6.4 8.6 4.6 6.6 Q3.4 5 4 3.2Z" fill="var(--white)"/></svg>
      555-014-2290
    </li>
    <li>
      <svg viewBox="0 0 12 12" aria-hidden="true"><circle cx="6" cy="6" r="6" fill="var(--royal)"/><rect x="3" y="4" width="6" height="4.2" fill="var(--white)"/><path d="M3 4 L6 6.4 L9 4" fill="none" stroke="var(--royal)" stroke-width="0.7"/></svg>
      aldren@aldrenhalejewelry.com
    </li>
    <li>
      <svg viewBox="0 0 12 12" aria-hidden="true"><circle cx="6" cy="6" r="6" fill="var(--royal)"/><circle cx="6" cy="6" r="3.2" fill="none" stroke="var(--white)" stroke-width="0.8"/><path d="M2.8 6 H9.2 M6 2.8 V9.2" stroke="var(--white)" stroke-width="0.8"/></svg>
      www.aldrenhalejewelry.com
    </li>
  </ul>

  <p class="store-address">2280 Marlow Avenue<br>Bayview, FL 32000</p>
</section>

<section class="card card-back" aria-label="Business card back">
  <div class="wordmark">
    <span class="wordmark-name">Aldren Hale</span>
    <span class="wordmark-tag">FINE JEWELRY</span>
  </div>
  <p class="back-domain">aldrenhalejewelry.com</p>
  <p class="back-website">www.aldrenhalejewelry.com</p>
</section>

</body>
</html>
```